Ward Compass Business Card Design*

We need a business card design for our company Ward Compass. Our company is specialized in providing online consulting services regarding medical institutions, hospitals and doctors. We work with patients worldwide looking to choose between healthcare providers. We have a website you may use as a reference, where we list doctors and clinics worldwide. So we target Medical providers as well as patients worldwide.
Target Market(s)
Medical Providers and patients around the world
Industry/Entity Type
Medical
Contact Information for Business Card
Salwa Kettani
CEO
+90 612 348 2175
info@wardcompass.example
www.wardcompass.example
14 Annakhil 7 H.R.B. Rabat, Morocco
Requirements
Must have
- Company logo/name on one full side, personal info and smaller logo and company name on the other side.
Nice to have
- Smart and elegant design

```html
<!DOCTYPE html>
<html lang="en">
<head>
<meta charset="utf-8">
<title>Ward Compass Business Card</title>
<link rel="stylesheet" href="https://fonts.googleapis.com/css2?family=Lato:wght@400;700&display=swap">
<style>
  :root {
    --stage: #c9c9c9;
    --brand-blue: #2e78b9;
    --accent-blue: #33a6d8;
    --card-white: #ffffff;
    --text-light: #ffffff;
  }
  * { margin: 0; padding: 0; box-sizing: border-box; }
  html, body { width: 1200px; height: 802px; overflow: hidden; }
  body {
    background: var(--stage);
    position: relative;
    font-family: "Lato", sans-serif;
  }
  .card {
    position: absolute;
    top: 274px;
    width: 442px;
    height: 265px;
    box-shadow: 0 3px 8px rgba(0,0,0,0.35);
    overflow: hidden;
  }
  .card-front { left: 136px; background: var(--brand-blue); }
  .card-back { left: 624px; background: var(--card-white); }

  .person {
    position: absolute;
    left: 26px; top: 74px;
    color: var(--text-light);
  }
  .person-name { font-size: 16px; letter-spacing: 0.2px; line-height: 1; }
  .person-name strong { font-weight: 700; }
  .person-name span { font-weight: 400; }
  .person-role { font-size: 12.5px; margin-top: 2px; line-height: 1.1; }

  .contact-list {
    position: absolute;
    left: 26px; top: 142px;
    list-style: none;
    color: var(--text-light);
    font-size: 12.5px;
  }
  .contact-list li { display: flex; align-items: center; height: 16px; white-space: nowrap; }
  .contact-list svg { width: 11px; height: 11px; margin-right: 4px; fill: var(--text-light); flex: none; }

  .brand-small {
    position: absolute;
    right: 22px; top: 70px;
    display: flex; align-items: center;
    gap: 7px;
  }
  .brand-small .brand-dot {
    width: 26px; height: 26px; border-radius: 50%;
    background: var(--accent-blue);
  }
  .brand-small .brand-name {
    font-weight: 700;
    font-size: 14px;
    letter-spacing: 0.4px;
    color: var(--text-light);
  }

  .brand {
    position: absolute;
    inset: 0;
    display: flex; align-items: center; justify-content: center;
    gap: 10px;
  }
  .brand .brand-dot {
    width: 40px; height: 40px; border-radius: 50%;
    background: var(--brand-blue);
  }
  .brand .brand-name {
    font-weight: 700;
    font-size: 23px;
    color: var(--brand-blue);
    letter-spacing: 0.5px;
  }
</style>
</head>
<body>
  <section class="card card-front">
    <div class="person">
      <p class="person-name"><strong>SALWA</strong> <span>KETTANI</span></p>
      <p class="person-role">CEO</p>
    </div>
    <div class="brand-small">
      <div class="brand-dot"></div>
      <p class="brand-name">WARD COMPASS</p>
    </div>
    <ul class="contact-list">
      <li>
        <svg viewBox="0 0 12 12" aria-hidden="true"><path d="M1 4c0-2 2-3 5-3s5 1 5 3v1H8.5V4h-5v1H1zM3 6h6l1.5 5h-9z"/></svg>
        +90 612 348 2175
      </li>
      <li>
        <svg viewBox="0 0 12 12" aria-hidden="true"><path d="M1 2.5h10v7H1z"/><path d="M1.8 3.2 6 6.5l4.2-3.3" fill="none" stroke="#2e78b9" stroke-width="0.9"/></svg>
        info@wardcompass.example
      </li>
      <li>
        <svg viewBox="0 0 12 12" aria-hidden="true"><circle cx="6" cy="6" r="5.2"/><path d="M3 3.5c1 .5 2 0 2.5 1S4 6.5 5 7.5s.5 2.5 0 3M8 2c-.5 1 .5 2 1.5 2.2M8.5 7c.5.5 1.5 1 1.5 2" fill="none" stroke="#2e78b9" stroke-width="0.9"/></svg>
        www.wardcompass.example
      </li>
      <li>
        <svg viewBox="0 0 12 12" aria-hidden="true"><path d="M6 0.6a3.8 3.8 0 0 1 3.8 3.8C9.8 7.3 6 11.4 6 11.4S2.2 7.3 2.2 4.4A3.8 3.8 0 0 1 6 .6z"/><circle cx="6" cy="4.4" r="1.4" fill="#2e78b9"/></svg>
        14 Annakhil 7 H.R.B. Rabat, Morocco
      </li>
    </ul>
  </section>

  <section class="card card-back">
    <div class="brand">
      <div class="brand-dot"></div>
      <p class="brand-name">WARD COMPASS</p>
    </div>
  </section>
</body>
</html>
```